Brisk Fixwell business card

I need business card for my business, I think you have all my details.six months ago I design with you car wrap design. We would like to design both side of the card. On front of card we would like logo , Name and our contact details.
At the back we are looking to mentioned our services.
The name will be:
Faridoullan Mestor
Managing Director
Ph:07952338417
Email:info@brisk-fixwell.com
Web:www.brisk-fixwell.com
So we have our logo, you don’t need to change the logo.
Please see the attachment.
Thanks

Target Market(s)

Home improvement

Industry/Entity Type

Home Improvement

Contact Information for Business Card

Company name: Brisk Fixwell
Name: Faridoullan Mestor
Position: Director
Ph:07952338417
Web: www.brisk-fixwell.com
Add: 42 Corvale Road
Hounslow
TW3 9KD
SECOND PERSON
Nizamuddel mestor
Position: Handyman
Ph: 07812 564037
Email: info@brisk-fixwell.com
Add: 18 Brackwin Lane Road
Hounslow
TW6 2LB

```html
<!DOCTYPE html>
<html lang="en">
<head>
<meta charset="utf-8">
<title>Brisk Fixwell business card</title>
<link href="https://fonts.googleapis.com/css2?family=Roboto:wght@400;500;700&display=swap" rel="stylesheet">
<style>
  :root {
    --navy: #22265e;
    --navy-soft: #3a3f7a;
    --red: #c0201c;
    --paper: #f3f3f3;
    --backdrop: #d4d4d4;
    --white: #ffffff;
    --ink: #22265e;
  }
  * { box-sizing: border-box; margin: 0; padding: 0; }
  html, body {
    width: 1200px; height: 576px; overflow: hidden;
    background: var(--backdrop);
    font-family: "Roboto", Arial, sans-serif;
  }
  .canvas { position: relative; width: 1200px; height: 576px; }
  .card {
    position: absolute; top: 138px; width: 482px; height: 294px;
    border-radius: 10px; overflow: hidden;
  }
  /* Back side: services */
  .card-back { left: 82px; background: var(--navy); }
  .card-back .brand-mark {
    position: absolute; left: 0; right: 0; top: 108px;
    text-align: center; font-weight: 700; font-size: 30px;
    color: var(--navy-soft);
  }
  .services-band {
    position: absolute; left: 0; right: 0; bottom: 0; height: 46px;
    background: var(--red); color: var(--white);
    display: flex; flex-direction: column; justify-content: center; align-items: center;
    font-size: 13px; line-height: 16px;
  }
  /* Front side: contact */
  .card-front { left: 602px; background: var(--paper); }
  .card-front .brand-name {
    position: absolute; left: 30px; top: 46px;
    font-weight: 700; font-size: 34px; color: var(--navy); line-height: 1;
  }
  .card-front .accent-square {
    position: absolute; left: 332px; top: 64px; width: 115px; height: 115px;
    background: var(--red);
  }
  .person { position: absolute; left: 30px; top: 142px; }
  .person-name { font-weight: 700; font-size: 19px; color: var(--navy); }
  .person-role { font-size: 12.5px; color: var(--red); margin-top: 3px; }
  .contact-list { position: absolute; left: 32px; top: 203px; list-style: none; }
  .contact-list li {
    display: flex; align-items: center; gap: 11px;
    font-size: 12.5px; color: var(--ink); height: 18.5px;
  }
  .contact-list svg { width: 11px; height: 11px; fill: var(--red); flex: none; }
</style>
</head>
<body>
<div class="canvas">

  <section class="card card-back">
    <div class="brand-mark">Brisk Fixwell</div>
    <div class="services-band">
      <span>Electrical &nbsp;|&nbsp; Carpentry &nbsp;|&nbsp; Plumbing &nbsp;|&nbsp; Plastering &nbsp;|&nbsp; Flooring</span>
      <span>Fencing &nbsp;|&nbsp; Decking &nbsp;|&nbsp; Painting &amp; Decorating</span>
    </div>
  </section>

  <section class="card card-front">
    <div class="brand-name">Brisk Fixwell</div>
    <div class="accent-square"></div>
    <div class="person">
      <div class="person-name">Faridoullan Mestor</div>
      <div class="person-role">Managing Director</div>
    </div>
    <ul class="contact-list">
      <li>
        <svg viewBox="0 0 12 12" aria-hidden="true"><path d="M1 4c0-2 2-3 5-3s5 1 5 3v1H8V4H4v1H1z M2.5 6h7l1 5h-9z"/></svg>
        07952338417
      </li>
      <li>
        <svg viewBox="0 0 12 12" aria-hidden="true"><path d="M0 2h12v8H0z" fill="var(--red)"/><path d="M0 2l6 5 6-5" fill="none" stroke="#f3f3f3" stroke-width="1.2"/></svg>
        info@brisk-fixwell.com
      </li>
      <li>
        <svg viewBox="0 0 12 12" aria-hidden="true"><circle cx="6" cy="6" r="5.5"/><path d="M0.5 6h11M6 0.5v11M2 3h8M2 9h8" stroke="#f3f3f3" stroke-width="0.8" fill="none"/><ellipse cx="6" cy="6" rx="2.4" ry="5.5" fill="none" stroke="#f3f3f3" stroke-width="0.8"/></svg>
        www.brisk-fixwell.com
      </li>
    </ul>
  </section>

</div>
</body>
</html>
```